New look and feel for a Website, mobile design, desktop design

We do a redesign of the website korlavin.com. We expect the designer to come up with ideas about a new look AND feel.
Starting point of the designers considerations should be the mobile design. Even though we are not creating a mobile App, the designer should think of it as one regarding design and usability. Using responsive design technology, we will shift from the mobile design to the desktop design and likewise. So the designer is supposed to come up with a solution for that as well.
What we expect
- definition of single design-elements that can be used in various places
- creation of a mobile design for all different types of pages
- creation of a desktop design for all different types of pages
Find a detailed description in the redesign-specification.

Target Market(s)

Germany, Austria, Switzerland

Industry/Entity Type

Residential Construction

Number of Pages Required

5+ page

Font styles to use
Other font styles liked:
• Open Sans

Colors

Designer to choose colors to be used in the design.

Requirements
Must have
• - mobile design concept
• - desktop design concept
• More information see document "Redesign-korlavin-specification.doc"

```html
<!DOCTYPE html>
<html lang="de">
<head>
<meta charset="utf-8">
<title>korlavin – Badrenovierung</title>
<link href="https://fonts.googleapis.com/css2?family=Montserrat:wght@400;500;600;700&family=Open+Sans:wght@400;600;700&display=swap" rel="stylesheet">
<style>
:root{
  --orange:#e8720c;
  --blue:#1a8fd6;
  --navy:#0f4f86;
  --footer:#1266b4;
  --ink:#222a33;
  --muted:#5a6470;
  --grey:#eeeff1;
  --line:#dde1e6;
  --white:#ffffff;
}
*{box-sizing:border-box;margin:0;padding:0}
html,body{width:1200px;height:3579px;overflow:hidden}
body{font-family:"Open Sans",Arial,sans-serif;color:var(--ink);background:var(--white);position:relative}
.sec{position:absolute;left:0;width:1200px}
h2.section-title{font-family:"Montserrat",Arial,sans-serif;font-weight:700;font-size:20px;letter-spacing:.5px;text-align:center;text-transform:uppercase}
.rule{width:52px;height:3px;background:var(--blue);margin:14px auto 0}

/* header */
.header{top:0;height:120px;background:var(--white)}
.brand{position:absolute;left:131px;top:22px;display:flex;flex-direction:column;align-items:center;gap:6px}
.brand-dot{width:42px;height:42px;border-radius:50%;background:var(--blue)}
.brand-name{font-family:"Montserrat",Arial,sans-serif;font-weight:600;font-size:30px;color:var(--navy);line-height:1}
.call{position:absolute;left:612px;top:24px;font-family:"Montserrat",Arial,sans-serif;font-size:12px;font-weight:700;color:var(--ink);display:flex;align-items:center;gap:8px}
.call-bar{position:absolute;left:612px;top:46px;width:456px;height:2px;background:var(--line)}
.phones{position:absolute;left:612px;top:50px;display:flex;gap:30px;font-family:"Montserrat",Arial,sans-serif;font-weight:600;font-size:16px;color:var(--navy)}
.phones span{display:flex;align-items:center;gap:8px}
.nav{position:absolute;right:130px;top:90px;display:flex;gap:26px;font-family:"Montserrat",Arial,sans-serif;font-size:13px;font-weight:500}

/* hero */
.hero{top:120px;height:548px;background:linear-gradient(100deg,#8c6a48 0%,#c9a57e 30%,#3a3028 48%,#b48658 70%,#d9c4a4 100%)}
.hero-title{position:absolute;top:200px;width:100%;text-align:center;font-family:"Montserrat",Arial,sans-serif;font-weight:700;font-size:34px;color:var(--white);letter-spacing:1px}
.hero-actions{position:absolute;top:268px;width:100%;display:flex;justify-content:center;gap:12px}
.btn{font-family:"Montserrat",Arial,sans-serif;font-weight:700;font-size:15px;color:var(--white);padding:14px 28px;text-transform:uppercase}
.btn-orange{background:var(--orange)}
.btn-blue{background:var(--blue)}
.dots{position:absolute;top:478px;width:100%;display:flex;justify-content:center;gap:14px}
.dots i{width:9px;height:9px;border-radius:50%;background:#fff}
.dots i.on{background:var(--orange)}

/* finder */
.finder{top:668px;height:115px;display:flex;align-items:center;padding-left:150px;gap:30px}
.finder-label{font-family:"Montserrat",Arial,sans-serif;font-size:19px;font-weight:500}
.finder-field{display:flex;width:427px;height:47px;border:1px solid var(--line)}
.finder-field span{flex:1;padding:14px;font-size:12px;color:var(--muted)}
.finder-field b{width:48px;background:var(--orange);display:flex;align-items:center;justify-content:center}
.finder-link{background:var(--blue);color:#fff;font-family:"Montserrat",Arial,sans-serif;font-weight:600;font-size:13px;padding:15px 28px}

/* offers */
.offers{top:783px;height:498px;background:var(--grey)}
.offers h2{margin-top:58px}
.offers-sub{text-align:center;font-size:14px;color:var(--muted);margin-top:6px}
.offer{position:absolute;top:147px;width:358px;height:287px;background:#fff;box-shadow:0 2px 8px rgba(0,0,0,.08);text-align:center}
.offer-badge{height:170px;display:flex;flex-direction:column;justify-content:center;align-items:center;font-family:"Montserrat",Arial,sans-serif;color:var(--orange)}
.offer-badge strong{font-size:54px;font-weight:700;line-height:1}
.offer-badge span{font-size:22px;font-weight:600}
.offer hr{border:0;border-top:1px solid var(--line);margin:0 36px}
.offer p{font-size:13px;color:var(--muted);line-height:1.6;padding:22px 70px 0}

/* welcome */
.welcome{top:1281px;height:492px}
.welcome h2{position:absolute;left:148px;top:72px;font-family:"Montserrat",Arial,sans-serif;font-weight:700;font-size:18px;text-transform:uppercase}
.welcome .rule{position:absolute;left:148px;top:98px;margin:0}
.welcome-copy{position:absolute;left:148px;top:130px;width:600px;font-size:13px;color:var(--muted);line-height:1.65}
.welcome ul{list-style:none;margin-top:22px}
.welcome li{position:relative;padding-left:30px;margin-bottom:14px;max-width:420px}
.welcome li::before{content:"";position:absolute;left:0;top:7px;width:6px;height:6px;border-top:2px solid var(--blue);border-right:2px solid var(--blue);transform:rotate(45deg)}
.welcome-mark{position:absolute;left:780px;top:64px;width:260px;height:260px;border-radius:50%;background:#e6f1fb;display:flex;align-items:center;justify-content:center;font-family:"Montserrat",Arial,sans-serif;font-weight:600;font-size:34px;color:var(--blue)}

/* stats */
.stats{top:1773px;height:370px;background:linear-gradient(135deg,#0e4e82,#13609c 60%,#0c4676)}
.stats h2{color:#fff;margin-top:52px}
.stat-row{position:absolute;top:152px;left:130px;width:940px;display:flex;justify-content:space-between}
.stat{width:140px;text-align:center;color:#fff}
.stat-ring{width:114px;height:114px;margin:0 auto;border-radius:50%;border:5px solid var(--blue);display:flex;align-items:center;justify-content:center;font-family:"Montserrat",Arial,sans-serif;font-size:32px;font-weight:500}
.stat-ring sup{font-size:14px}
.stat p{margin-top:16px;font-size:14px}

/* recommendations */
.reco{top:2143px;height:482px}
.reco h2{margin-top:42px}
.reco-track{position:absolute;top:143px;left:131px;display:flex;gap:10px}
.reco-card{width:228px;height:279px;border:1px solid var(--line);background:#fff;padding:6px}
.reco-photo{height:208px}
.reco-card p{font-size:13px;padding:12px 8px 0;line-height:1.4}
.arrow{position:absolute;top:262px}
.arrow svg{display:block}

/* blog */
.blog{top:2625px;height:572px;background:var(--grey)}
.blog h2{margin-top:50px}
.post{position:absolute;top:148px;width:293px}
.post-photo{height:193px}
.post h3{font-family:"Montserrat",Arial,sans-serif;font-size:14px;font-weight:600;margin-top:18px;line-height:1.35}
.post p{font-size:11.5px;color:var(--muted);line-height:1.6;margin-top:8px;height:56px;overflow:hidden}
.post .more{display:inline-block;margin-top:16px;background:var(--orange);color:#fff;font-family:"Montserrat",Arial,sans-serif;font-weight:700;font-size:11px;padding:7px 12px;text-transform:uppercase}

/* footer */
.footer{top:3197px;height:382px;background:var(--footer);color:#fff}
.footer-brand{position:absolute;left:150px;top:62px;display:flex;flex-direction:column;align-items:center;gap:10px}
.footer-brand .brand-dot{width:60px;height:60px;background:#fff}
.footer-brand .brand-name{color:#fff;font-size:36px}
.footer h4{font-family:"Montserrat",Arial,sans-serif;font-size:12px;font-weight:700;text-transform:uppercase}
.contact{position:absolute;left:400px;top:57px;font-size:11px}
.contact div{display:flex;gap:12px;margin-top:18px;line-height:1.5}
.menu{position:absolute;left:685px;top:57px;font-size:11px}
.menu ul{list-style:none;margin-top:14px;line-height:1.6}
.chat{position:absolute;left:896px;top:57px;width:156px;height:46px;background:var(--orange);display:flex;align-items:center;justify-content:center;gap:8px;font-family:"Montserrat",Arial,sans-serif;font-weight:700;font-size:14px}
.follow{position:absolute;left:896px;top:138px;width:156px;text-align:center}
.socials{display:flex;justify-content:center;gap:10px;margin-top:16px}
.socials i{width:26px;height:26px;border-radius:50%;background:#fff;opacity:.9}
.footer-line{position:absolute;left:131px;right:131px;top:268px;height:1px;background:rgba(255,255,255,.25)}
.copyright{position:absolute;top:312px;width:100%;text-align:center;font-size:11px}
</style>
</head>
<body>

<header class="sec header">
  <div class="brand"><span class="brand-dot"></span><span class="brand-name">korlavin</span></div>
  <div class="call">
    <svg width="14" height="14" viewBox="0 0 24 24"><path fill="#222a33" d="M6.6 10.8a15 15 0 0 0 6.6 6.6l2.2-2.2c.3-.3.7-.4 1-.2 1.1.4 2.3.6 3.6.6.6 0 1 .4 1 1V20c0 .6-.4 1-1 1A17 17 0 0 1 3 4c0-.6.4-1 1-1h3.5c.6 0 1 .4 1 1 0 1.3.2 2.5.6 3.6.1.3 0 .7-.2 1z"/></svg>
    CALL US NOW
  </div>
  <div class="call-bar"></div>
  <div class="phones">
    <span><svg width="20" height="13"><rect width="20" height="13" fill="#d52b1e"/><rect y="4.3" width="20" height="4.4" fill="#fff"/></svg>0800 31 47 52</span>
    <span><svg width="20" height="13"><rect width="20" height="4.3" fill="#111"/><rect y="4.3" width="20" height="4.4" fill="#d00"/><rect y="8.7" width="20" height="4.3" fill="#fc0"/></svg>0800 36 58 914</span>
    <span><svg width="14" height="14"><rect width="14" height="14" fill="#d52b1e"/><rect x="5.5" y="2.5" width="3" height="9" fill="#fff"/><rect x="2.5" y="5.5" width="9" height="3" fill="#fff"/></svg>0800 27 63 41</span>
  </div>
  <nav class="nav"><span>Badlösungen</span><span>Badinformationen</span><span>Messen</span><span>Kundenmeinungen</span><span>Standorte</span><span>Presse</span><span>über korlavin</span></nav>
</header>

<section class="sec hero" role="img" aria-label="Foto eines alten, gefliesten Badezimmers mit Badewanne und Duschkabine vor der Renovierung">
  <h1 class="hero-title">BATHROOM RENOVATION</h1>
  <div class="hero-actions"><span class="btn btn-orange">Contact us</span><span class="btn btn-blue">Free consultation</span></div>
  <div class="dots"><i></i><i></i><i class="on"></i><i></i><i></i></div>
</section>

<section class="sec finder">
  <span class="finder-label">korlavin in Ihrer Nähe</span>
  <div class="finder-field"><span>PLZ eingeben</span><b><svg width="18" height="18" viewBox="0 0 24 24"><circle cx="10" cy="10" r="6.5" fill="none" stroke="#fff" stroke-width="2.5"/><path d="M15 15l6 6" stroke="#fff" stroke-width="2.5"/></svg></b></div>
  <span class="finder-link">zur Partnerübersicht wechseln</span>
</section>

<section class="sec offers">
  <h2 class="section-title">Ein neues Bad in 24 Stunden</h2>
  <p class="offers-sub">mit korlavin Systemlösungen zur Badrenovierung</p>
  <article class="offer" style="left:217px">
    <div class="offer-badge"><strong>24h</strong><span>Bad-Renovierung</span></div>
    <hr>
    <p>Ein neues Bad, barrierefrei und seniorengerecht! Und das innerhalb von 24 Arbeitsstunden!</p>
  </article>
  <article class="offer" style="left:620px">
    <div class="offer-badge"><strong>8h</strong><span>Dusch-Renovierung</span></div>
    <hr>
    <p>Wanne raus, Dusche rein! Oder einfach nur eine neue Dusche innerhalb eines Tages!</p>
  </article>
</section>

<section class="sec welcome">
  <h2>Welcome to our site</h2>
  <div class="rule"></div>
  <div class="welcome-copy">
    <p>Unsere Mission bei korlavin ist es, mit allen Mitteln und Möglichkeiten zu helfen, dass unsere Kunden und Wegbegleiter besser leben.</p>
    <ul>
      <li>And our employees also benefit from this concept</li>
      <li>Because to be successful does not mean that we only have one's career in mind</li>
      <li>Every employee at korlavin has its own story. Representing the more than 500 employees in the korlavin group, some of them talk about their very personal experiences at this point.</li>
    </ul>
  </div>
  <div class="welcome-mark">korlavin</div>
</section>

<section class="sec stats">
  <h2 class="section-title">Kundenzufriedenheit</h2>
  <div class="rule"></div>
  <div class="stat-row">
    <div class="stat"><div class="stat-ring">132</div><p>Bewertungen</p></div>
    <div class="stat"><div class="stat-ring">99<sup>%</sup></div><p>Beratung</p></div>
    <div class="stat"><div class="stat-ring">99<sup>%</sup></div><p>Ausführung</p></div>
    <div class="stat"><div class="stat-ring">99<sup>%</sup></div><p>Termintreue</p></div>
    <div class="stat"><div class="stat-ring">97<sup>%</sup></div><p>Preis/Leistung</p></div>
  </div>
</section>

<section class="sec reco">
  <h2 class="section-title">Empfehlungen</h2>
  <div class="rule"></div>
  <div class="arrow" style="left:76px"><svg width="16" height="30"><path d="M13 2L3 15l10 13" fill="none" stroke="#b8bec6" stroke-width="2.5"/></svg></div>
  <div class="reco-track">
    <div class="reco-card"><div class="reco-photo" role="img" aria-label="Foto einer Dusche mit grünen Wandpaneelen" style="background:linear-gradient(160deg,#5d6d66,#8e9c95)"></div><p>Empfehlung von<br>Familie Brenner</p></div>
    <div class="reco-card"><div class="reco-photo" role="img" aria-label="Foto einer hellen Dusche mit Glaswand" style="background:linear-gradient(160deg,#d8dde2,#a9b1b9)"></div><p>Empfehlung von<br>Herrn Kessler</p></div>
    <div class="reco-card"><div class="reco-photo" role="img" aria-label="Foto einer Dusche mit roter Rückwand" style="background:linear-gradient(160deg,#a8343a,#e4d9cf)"></div><p>Empfehlung von<br>Herrn Kessler</p></div>
    <div class="reco-card"><div class="reco-photo" role="img" aria-label="Foto eines Bads mit orangefarbener Wand" style="background:linear-gradient(160deg,#e2681e,#f2ede6 70%,#2b2b2b)"></div><p>Empfehlung von<br>Frau Lorenz</p></div>
  </div>
  <div class="arrow" style="left:1106px"><svg width="16" height="30"><path d="M3 2l10 13L3 28" fill="none" stroke="#b8bec6" stroke-width="2.5"/></svg></div>
</section>

<section class="sec blog">
  <h2 class="section-title">Latest blog</h2>
  <div class="rule"></div>
  <article class="post" style="left:131px">
    <div class="post-photo" role="img" aria-label="Foto eines Bads mit Wandpaneelen und freistehender Wanne" style="background:linear-gradient(160deg,#cfd1cf,#9aa09d)"></div>
    <h3>Fugenloses Bad – durch Wandpaneele Probleme vermeiden</h3>
    <p>Durch den Ersatz der alten Badewanne durch eine neue bodenebene Dusche können Herr und Frau Stein nun entspannt duschen.</p>
    <span class="more">Read more</span>
  </article>
  <article class="post" style="left:453px">
    <div class="post-photo" role="img" aria-label="Foto einer Badausstellung mit Duschkabinen" style="background:linear-gradient(160deg,#e07428,#cfcac4 40%,#4b4f55)"></div>
    <h3>Die Badausstellung ganz in Ihrer Nähe</h3>
    <p>Sie haben sich zu einer Badrenovierung entschlossen? Gratulation! Wenn Sie nun im Internet nach Inspiration für Ihr künftiges Bad suchen, kann schnell das Gefühl entstehen…</p>
    <span class="more">Read more</span>
  </article>
  <article class="post" style="left:775px">
    <div class="post-photo" role="img" aria-label="Foto eines kleinen Bads mit orangefarbener Wand und Waschtisch" style="background:linear-gradient(160deg,#d9662a,#ece6df 55%,#b9b3ac)"></div>
    <h3>Kleine Bäder einrichten – Tipps und Tricks</h3>
    <p>Gerade bei älteren Wohnungen oder Häusern sind Bäder oft nicht besonders groß. Es ist eine gewisse Herausforderung, kleine Bäder einzurichten, aber mit etwas Kreativität kann…</p>
    <span class="more">Read more</span>
  </article>
</section>

<footer class="sec footer">
  <div class="footer-brand"><span class="brand-dot"></span><span class="brand-name">korlavin</span></div>
  <div class="contact">
    <h4>Contact us</h4>
    <div><svg width="12" height="14" viewBox="0 0 24 28"><path fill="#fff" d="M12 0a10 10 0 0 0-10 10c0 7.5 10 18 10 18s10-10.5 10-18A10 10 0 0 0 12 0zm0 14a4 4 0 1 1 0-8 4 4 0 0 1 0 8z"/></svg><span>Lindenweg 12,<br>08150 Talbach im Erzland</span></div>
    <div><svg width="12" height="12" viewBox="0 0 24 24"><path fill="#fff" d="M6.6 10.8a15 15 0 0 0 6.6 6.6l2.2-2.2c.3-.3.7-.4 1-.2 1.1.4 2.3.6 3.6.6.6 0 1 .4 1 1V20c0 .6-.4 1-1 1A17 17 0 0 1 3 4c0-.6.4-1 1-1h3.5c.6 0 1 .4 1 1 0 1.3.2 2.5.6 3.6.1.3 0 .7-.2 1z"/></svg><span>0800 36 58 914</span></div>
    <div><svg width="12" height="10" viewBox="0 0 24 18"><rect width="24" height="18" rx="2" fill="#fff"/><path d="M1 1l11 9 11-9" fill="none" stroke="#1266b4" stroke-width="2"/></svg><span>info@korlavin.com</span></div>
  </div>
  <div class="menu">
    <h4>Menu</h4>
    <ul><li>Badlösungen</li><li>Badinformationen</li><li>Messen</li><li>Kundenmeinungen</li><li>Standorte</li><li>Presse</li><li>Über korlavin</li></ul>
  </div>
  <div class="chat"><svg width="18" height="18" viewBox="0 0 24 24"><path d="M4 14v-2a8 8 0 0 1 16 0v2" fill="none" stroke="#fff" stroke-width="2.5"/><rect x="2" y="13" width="5" height="7" rx="1.5" fill="#fff"/><rect x="17" y="13" width="5" height="7" rx="1.5" fill="#fff"/></svg>LIVE CHAT</div>
  <div class="follow"><h4>Follow us</h4><div class="socials"><i></i><i></i><i></i></div></div>
  <div class="footer-line"></div>
  <p class="copyright">Copyrights @ 2018 All Rights Reserved</p>
</footer>

</body>
</html>
```